Pizza Coupon App Design Project

*******This project will have a guaranteed payout once I see that there is quality work being designed*********

I require the design (no coding) of 4 vertical screens (the screen will not change for horizontal orientation) for Zentrix and Orbalis. The highest res should be used so it can be scaled for older generation phones.

The mobile app will be used to access pizza coupons.

I do not have a specific style or look that I am going for, although I do not want a childish design (e.g. comic sans). The main requirements are for it to be very easy for users to understand and navigate and to be clean and professional.

I am happy if you only produce a design of the main and store selection screens to which I will give feedback before continuing to design the remaining screens.

The selected artist must be flexible in adapting the final design slightly after the contest is completed, during the app development process (maybe a few small modifications over a month or so).
Please do not include any copyrighted images in your deliverables. I must be the sole owner of the graphics once I have paid for them.

I have included attachments which show the process flow and the screen requirements so that will give you the detail you need to design them. I have also included the logo to assist you in your design., *******This project is now guaranteed *********

I have included attachments which show the process flow and the screen requirements so that will give you the detail you need to design them. I have also included the logo to assist you in your design., *******This project will have a guaranteed payout once I see that there is quality work being designed*********

I have included attachments which show the process flow and the screen requirements so that will give you the detail you need to design them. I have also included the logo to assist you in your design.

Reason: Still looking for the perfect design! ******Project is now guaranteed******

******Project is now guaranteed******

Reason: Starting to get some great designs, we are getting much closer! Keep it up.

Target Market(s)

students and 18-30 year olds - People who want cheap meals and people who order pizza online., students and 18-30 year olds - People who want cheap meals and people who order pizza online., students and 18-30 year olds - People who want cheap meals and people who order pizza online.

Industry/Entity Type

Store

Requirements
Must have
• Must have requirements are listed in the attached documents., Must have requirements are listed in the attached documents., Must have requirements are listed in the attached documents.

```html
<!DOCTYPE html>
<html lang="en">
<head>
<meta charset="utf-8">
<title>Pizza Coupons – Store 1</title>
<link rel="stylesheet" href="https://fonts.googleapis.com/css2?family=Open+Sans:wght@400;600;700;800&display=swap">
<style>
  :root{
    --page:#e9e7e4;
    --screen:#f2efeb;
    --banner-top:#4b4b4b;
    --banner-bottom:#6b6b6b;
    --banner-text:#8e8e8e;
    --ink:#2c2c2c;
    --muted:#5c4a2e;
    --pale-yellow:#fbc84f;
    --pale-yellow-2:#f7b52c;
    --yellow:#fcd22e;
    --yellow-2:#f5b81b;
    --brown:#6b3a17;
    --brown-2:#4a2610;
    --orange:#f59a3a;
    --orange-2:#e8782a;
    --red:#d2382b;
    --red-2:#a8231a;
    --green:#63b52b;
    --green-2:#3f8f16;
    --stub-box:#f5b54a;
    --track:#3a3a3a;
    --thumb:#c24a47;
    --icon:#3b3b3b;
  }
  *{box-sizing:border-box;margin:0;padding:0}
  html,body{width:1200px;height:949px;overflow:hidden}
  body{background:var(--page);font-family:"Open Sans",Arial,sans-serif;display:flex;justify-content:center;align-items:center}

  .screen{position:relative;width:600px;height:909px;background:var(--screen);overflow:hidden;box-shadow:0 2px 14px rgba(0,0,0,.18)}

  .ad-banner{height:130px;background:linear-gradient(var(--banner-top),var(--banner-bottom));display:flex;align-items:center;justify-content:center;color:var(--banner-text);font-size:34px;font-weight:400;letter-spacing:.5px}

  .toolbar{height:66px;display:flex;justify-content:flex-end;align-items:center;padding:0 70px 0 24px}
  .order-select{display:flex;align-items:center;height:46px;width:250px;border:2px solid #8d8d8d;border-radius:12px;background:linear-gradient(#fbfbfb,#d9d9d9);overflow:hidden;color:var(--ink)}
  .order-select .basket{width:46px;display:flex;justify-content:center}
  .order-select .label{flex:1;font-size:26px;padding-left:8px}
  .order-select .caret{width:56px;height:100%;display:flex;align-items:center;justify-content:center;background:linear-gradient(#d6d6d6,#a9a9a9);border-left:1px solid #8d8d8d}

  .store-heading{height:58px;display:flex;align-items:center;gap:14px;padding-left:26px;font-size:32px;color:var(--ink);font-weight:400}

  .coupon-list{list-style:none;padding:0 84px 0 22px;display:flex;flex-direction:column;gap:12px}
  .coupon{position:relative;display:flex;height:130px;filter:drop-shadow(0 2px 2px rgba(0,0,0,.25))}
  .coupon::before,.coupon::after{content:"";position:absolute;left:0;right:0;height:6px;z-index:2;
    background:radial-gradient(circle at 5px 0,var(--screen) 3px,transparent 3.5px) repeat-x;background-size:10px 6px}
  .coupon::before{top:0}
  .coupon::after{bottom:0;transform:scaleY(-1)}

  .offer{flex:1;position:relative;padding:20px 18px 12px 26px;display:flex;flex-direction:column;justify-content:center}
  .offer::before,.stub::before{content:"";position:absolute;inset:8px;border:1px dashed rgba(255,255,255,.35);border-radius:4px;pointer-events:none}
  .offer-text{font-size:20px;line-height:1.12;font-weight:800;text-transform:uppercase;letter-spacing:-.2px}
  .shared{margin-top:6px;font-size:13px;font-weight:400}
  .shared b{font-weight:700;margin-left:10px}

  .stub{position:relative;width:176px;display:flex;flex-direction:column;align-items:center;justify-content:center;color:#fff;border-left:2px dashed rgba(0,0,0,.25)}
  .stub-label{font-size:13px;font-weight:600;margin-bottom:2px}
  .code-box{position:relative;width:128px;height:46px;background:var(--stub-box);border:3px dashed #3a2410;border-radius:8px;display:flex;align-items:center;justify-content:center;color:#3a2410;font-size:19px;letter-spacing:1px}
  .code-box .scissors{position:absolute;left:-20px;top:4px}
  .price{margin-top:4px;font-weight:800;font-size:26px;text-shadow:0 1px 1px rgba(0,0,0,.35)}
  .price small{font-size:16px;margin-right:4px}

  .coupon--pale .offer{background:linear-gradient(var(--pale-yellow),var(--pale-yellow-2));color:#8a4a12}
  .coupon--yellow .offer{background:linear-gradient(var(--yellow),var(--yellow-2));color:#7a4210}
  .coupon--brown .offer{background:linear-gradient(var(--brown),var(--brown-2));color:#fff}
  .coupon--brown .shared{color:#e7c98a}
  .coupon--brown .shared b{color:#f4c233}
  .coupon--orange .offer{background:linear-gradient(var(--orange),var(--orange-2));color:#6a300c}
  .offer .shared{color:inherit}
  .offer .shared b{color:#3c2410}
  .coupon--brown .offer .shared b{color:#f4c233}

  .stub--brown{background:linear-gradient(#7a4520,#4d2a10)}
  .stub--red{background:linear-gradient(var(--red),var(--red-2))}
  .stub--green{background:linear-gradient(var(--green),var(--green-2))}
  .stub--green .price{color:#2f5a10;text-shadow:0 1px 0 rgba(255,255,255,.3)}
  .stub--green .stub-label{color:#2f4a12}

  .scrollbar{position:absolute;right:30px;top:214px;width:18px;height:600px;border-radius:9px;background:var(--track);border:2px solid #6c6c6c;overflow:hidden}
  .scrollbar .thumb{height:150px;background:linear-gradient(90deg,#a83733,var(--thumb),#a83733);border-radius:8px}

  .footer{position:absolute;left:0;right:0;bottom:0;height:70px;display:flex;justify-content:space-between;align-items:center;padding:0 26px 0 28px}
</style>
</head>
<body>
  <main class="screen">
    <header class="ad-banner">Advertising</header>

    <div class="toolbar">
      <div class="order-select">
        <span class="basket">
          <svg width="30" height="26" viewBox="0 0 30 26" fill="none" stroke="#444" stroke-width="2.2" stroke-linejoin="round">
            <path d="M9 11 L15 3 L21 11"/><path d="M3 11 H27 L24 23 H6 Z"/>
          </svg>
        </span>
        <span class="label">Pickup</span>
        <span class="caret">
          <svg width="22" height="14" viewBox="0 0 22 14"><path d="M1 1 H21 L11 13 Z" fill="#4a4a4a"/></svg>
        </span>
      </div>
    </div>

    <h1 class="store-heading">
      <svg width="42" height="38" viewBox="0 0 42 38">
        <path d="M3 2 H39 L41 12 H1 Z" fill="var(--icon)"/>
        <path d="M1 12 Q6 18 11 12 Q16 18 21 12 Q26 18 31 12 Q36 18 41 12 V15 H1Z" fill="var(--icon)"/>
        <rect x="4" y="18" width="34" height="18" fill="var(--icon)"/>
        <rect x="9" y="22" width="12" height="14" fill="var(--screen)"/>
      </svg>
      STORE 1
    </h1>

    <ul class="coupon-list">
      <li class="coupon coupon--pale">
        <div class="offer">
          <p class="offer-text">What you get for using the coupon. What you’ll get for using the coupoun.</p>
          <p class="shared">Shared by: <b>example-user</b></p>
        </div>
        <div class="stub stub--brown">
          <span class="stub-label">Copy code:</span>
          <span class="code-box"><svg class="scissors" width="34" height="24" viewBox="0 0 34 24" fill="none" stroke="#1f1f1f" stroke-width="2.5"><circle cx="6" cy="6" r="4"/><circle cx="6" cy="18" r="4"/><path d="M9 8 L32 18 M9 16 L32 6"/></svg>XXXXXX</span>
          <span class="price"><small>AU$</small>5.00</span>
        </div>
      </li>
      <li class="coupon coupon--yellow">
        <div class="offer">
          <p class="offer-text">What you get for using the coupon. What you’ll get for using the coupoun.</p>
          <p class="shared">Shared by: <b>example-user</b></p>
        </div>
        <div class="stub stub--red">
          <span class="stub-label">Copy code:</span>
          <span class="code-box"><svg class="scissors" width="34" height="24" viewBox="0 0 34 24" fill="none" stroke="#1f1f1f" stroke-width="2.5"><circle cx="6" cy="6" r="4"/><circle cx="6" cy="18" r="4"/><path d="M9 8 L32 18 M9 16 L32 6"/></svg>XXXXXX</span>
          <span class="price"><small>AU$</small>15.00</span>
        </div>
      </li>
      <li class="coupon coupon--brown">
        <div class="offer">
          <p class="offer-text">What you get for using the coupon. What you’ll get for using the coupoun.</p>
          <p class="shared">Shared by: <b>example-user</b></p>
        </div>
        <div class="stub stub--green">
          <span class="stub-label">Copy code:</span>
          <span class="code-box"><svg class="scissors" width="34" height="24" viewBox="0 0 34 24" fill="none" stroke="#1f1f1f" stroke-width="2.5"><circle cx="6" cy="6" r="4"/><circle cx="6" cy="18" r="4"/><path d="M9 8 L32 18 M9 16 L32 6"/></svg>XXXXXX</span>
          <span class="price"><small>AU$</small>15.00</span>
        </div>
      </li>
      <li class="coupon coupon--orange">
        <div class="offer">
          <p class="offer-text">What you get for using the coupon. What you’ll get for using the coupoun.</p>
          <p class="shared">Shared by: <b>example-user</b></p>
        </div>
        <div class="stub stub--red">
          <span class="stub-label">Copy code:</span>
          <span class="code-box"><svg class="scissors" width="34" height="24" viewBox="0 0 34 24" fill="none" stroke="#1f1f1f" stroke-width="2.5"><circle cx="6" cy="6" r="4"/><circle cx="6" cy="18" r="4"/><path d="M9 8 L32 18 M9 16 L32 6"/></svg>XXXXXX</span>
          <span class="price"><small>AU$</small>10.00</span>
        </div>
      </li>
    </ul>

    <div class="scrollbar"><div class="thumb"></div></div>

    <footer class="footer">
      <svg class="back-arrow" width="58" height="30" viewBox="0 0 58 30"><path d="M56 15 H10 M20 4 L6 15 L20 26" fill="none" stroke="var(--icon)" stroke-width="5" stroke-linecap="round" stroke-linejoin="round"/></svg>
      <svg class="settings" width="40" height="40" viewBox="0 0 40 40">
        <g fill="var(--icon)" transform="translate(20 20)">
          <rect x="-4" y="-19" width="8" height="10" rx="1"/>
          <rect x="-4" y="-19" width="8" height="10" rx="1" transform="rotate(45)"/>
          <rect x="-4" y="-19" width="8" height="10" rx="1" transform="rotate(90)"/>
          <rect x="-4" y="-19" width="8" height="10" rx="1" transform="rotate(135)"/>
          <rect x="-4" y="-19" width="8" height="10" rx="1" transform="rotate(180)"/>
          <rect x="-4" y="-19" width="8" height="10" rx="1" transform="rotate(225)"/>
          <rect x="-4" y="-19" width="8" height="10" rx="1" transform="rotate(270)"/>
          <rect x="-4" y="-19" width="8" height="10" rx="1" transform="rotate(315)"/>
          <circle r="13"/>
          <circle r="6" fill="var(--screen)"/>
        </g>
      </svg>
    </footer>
  </main>
</body>
</html>
```